Merrisol. Sunless Tanning Mousse Label

I'm looking for a label creation for a new brand of sunless tanning solutions. They are in 6.7oz bottles (template attached).

For the front of the bottle (see template) I would like an abstract multi coloured design taking up just over half the top of the bottle (approx 60%) and going around the design (this is similar to the design inspiration attached). I would this design to use the attached colour palette of pinks. It can be swirls, drips, squares, lines, whatever you think will look good.

The logo will then be over top of that abstract design in the upper 1/3, in the colour #3fe0d0

Under the abstract design the following text:

Amber Hush (Larger text)
Violet Base (2nd heading)
1 Hour Sunless Mousse (Sub text)
The No Orange Guarantee! (Sub text)
Vegan Formula (sub text)

The sub texts for above can be fun, have coloured background, different fonts, whatever looks good and is sill fun.

Towards the bottom of the front of bottle we require the sizing information:

200ml 6.7 Fl Oz

On the left side of the front (so in the template the middle smaller section) I would like the phrase "You ain't gotta get ready if you stay ready" Could you please make this as a separate little quote, with a fun design to it. It's like a little hidden gem on the side of the bottle.

On the back of the bottle for now can you please start towards the top with:

Amber Hush Mousse (larger)
Violet base (second heading)
Deep Mediterranean Inspired Tan (second heading)
Easy to Apply & Streak Free
Vegan friendly & 100% natural DHA tan actives

Under this I require approx 1.5" of Lorem Ipsum for now which will take the place of directions for using the product.

Under that in small writing can we include "Warning: This product does not contain a sunscreen and will not protect against sunburn. For external use only. If skin irritation occurs, discontinue use. Carry out a patch test 24 hours prior to full body use. Store below 25(degrees sign)C."

At the bottom is the smallest yet still legible writing, can we include the ingredients that are listed below.

Target Market(s)

Females 24-35 who take care of themselves and always want to look good. It's a youthful fun product.

Requirements
Must have
• Bright colours, and just screams FUN and youthful.

Ingredients must be listed on the back. They dont' need to take up more than an inch in height, less if possible.
*******************************************

INGREDIENTS: Water (Aqua), Propylene Glycol, Dihydroxyacetone, Peg-6 Caprylic/Capric Glycerides, Dihydroxypropyl Peg-5 Linoleammonium Chloride, Peg-7 Glyceryl Cocoate, Caramel,
Phenoxyethanol, Caprylyl Glycol, Potassium Sorbate, Hexylene Glycol, Glycerin, Helianthus Annuus (Sunflower) Seed Oil, Beta Vulgaris (Beet) Root Extract, Panthenol, Solanum Lycopersicum
(Tomato) Fruit Extract, Vaccinium Macrocarpon (Cranberry) Fruit Extract, L-ascorbic Acid (Vitamin C), Tocopheryl Acetate (Vitamin E), Theobroma Cacao (Cocoa) Seed Butter, Rosa Canina (Rose Hip)
Fruit Oil, Glycine Soja (Soybean) Oil, Cucumis Sativus (Cucumber) Fruit Extract, Blue 1 (CI 42090), Red 40 (CI 16035), Yellow 6 (CI 15985), Green 5 (CI 61570), Yellow 5 (CI 19140), Red 33 (CI 17200)

*****************************
Nice to have
• Several options to choose from, some can include a gradient into geometric shapes, rather than solid colour. Experiment
Should not have
• Do not want it to look medical.
Want colours to stay in the same pink family for the abstract design - can use white also.

```html
<!DOCTYPE html>
<html lang="en">
<head>
<meta charset="utf-8">
<title>Merrisol – Amber Hush Mousse Label</title>
<link href="https://fonts.googleapis.com/css2?family=Ubuntu:wght@500;700&family=Poppins:wght@400;500&family=Roboto+Condensed:wght@400&display=swap" rel="stylesheet">
<style>
  :root{
    --backdrop:#e0509a;
    --paper:#ffffff;
    --plum:#b2306f;
    --magenta:#c0157a;
    --rose:#c23d7c;
    --pill:#d94d8f;
    --ink:#222222;
    --cut:#111111;
    --hot:#f0138a;
    --berry:#b0148f;
    --mauve:#c0477a;
    --blush:#f48cb8;
    --wash-a:#f02488;
    --wash-b:#c8187f;
    --wash-c:#e8479c;
  }
  *{margin:0;padding:0;box-sizing:border-box}
  html,body{width:733px;height:1200px;overflow:hidden;background:var(--backdrop)}
  .sheet{position:absolute;left:11px;top:299px;width:1128px;height:955px;transform:scale(.63);transform-origin:0 0}
  .label{position:absolute;left:28px;top:25px;width:1074px;height:903px;background:var(--paper);overflow:hidden}
  .art-band{position:absolute;left:0;top:0;width:1074px;height:730px;
    background:linear-gradient(100deg,var(--wash-a) 0%,var(--wash-b) 35%,var(--wash-c) 65%,var(--wash-b) 100%)}
  .panel{position:absolute;background:var(--paper)}
  .panel--back{left:35px;top:137px;width:417px;height:723px}
  .panel--front{left:537px;top:547px;width:418px;height:200px}
  .quote-bar{position:absolute;left:477px;top:137px;width:39px;height:410px;background:var(--paper);display:flex;align-items:center;justify-content:center}
  .quote-bar span{writing-mode:vertical-rl;font-family:"Poppins",sans-serif;font-weight:500;font-size:14.5px;letter-spacing:.3px;color:var(--magenta);text-transform:uppercase;white-space:nowrap}
  .brand{position:absolute;left:537px;top:160px;width:418px;text-align:center;font-family:"Poppins",sans-serif;font-weight:500;font-size:82px;line-height:1;color:var(--paper);letter-spacing:1px}
  .title{font-family:"Ubuntu",sans-serif;font-weight:700;color:var(--plum);text-align:center;line-height:1}
  .variant{font-family:"Ubuntu",sans-serif;font-weight:700;color:var(--magenta);text-align:center;line-height:1}
  .back-content{position:absolute;left:35px;top:137px;width:417px}
  .back-content .title{font-size:51px;margin-top:64px;line-height:45px}
  .back-content .variant{font-size:31px;margin-top:8px}
  .tan{font-family:"Poppins",sans-serif;font-weight:400;font-size:28px;line-height:31px;color:var(--rose);text-align:center;margin-top:18px}
  .claims{list-style:none;margin:20px 0 0 70px;font-family:"Poppins",sans-serif;font-size:16.5px;line-height:19px;color:var(--magenta)}
  .claims li{display:flex;gap:8px;align-items:flex-start;margin-bottom:6px}
  .claims svg{flex:none;width:22px;height:22px;margin-top:-2px}
  .info{margin:18px 0 0 45px;width:330px;font-family:"Roboto Condensed",sans-serif;font-size:9.6px;line-height:12.2px;color:var(--ink);text-align:justify}
  .pill{display:inline-block;background:var(--pill);color:var(--paper);font-family:"Roboto Condensed",sans-serif;font-size:12.5px;padding:1px 11px;border-radius:10px;margin-bottom:3px;border:1.5px solid #f3a5c8}
  .info p{margin-bottom:10px}
  .front-content{position:absolute;left:537px;top:547px;width:418px}
  .front-content .title{font-size:51px;margin-top:48px}
  .front-content .variant{font-size:31px;margin-top:6px}
  .tags{position:relative;height:64px;margin-top:28px;font-family:"Poppins",sans-serif;font-size:13.5px;color:var(--paper)}
  .tag{position:absolute;height:20px;line-height:20px;text-align:center}
  .tag--time{left:70px;width:240px;top:0;background:linear-gradient(90deg,var(--mauve),var(--blush))}
  .tag--promise{left:105px;width:243px;top:21px;background:linear-gradient(90deg,var(--magenta),#c5377a)}
  .tag--vegan{left:70px;width:240px;top:42px;background:linear-gradient(90deg,var(--hot),var(--berry))}
  .size{font-family:"Poppins",sans-serif;font-size:17px;color:var(--plum);text-align:center;margin-top:42px}
  .dieline{position:absolute;left:0;top:0;width:1128px;height:955px;pointer-events:none}
</style>
</head>
<body>
<div class="sheet">
  <div class="label">
    <div class="art-band" role="img" aria-label="Abstract decorative pattern in pinks, magentas and purples wrapping the upper label"></div>

    <div class="panel panel--back"></div>
    <div class="panel panel--front"></div>

    <div class="quote-bar"><span>You ain’t gotta get ready if you stay ready</span></div>

    <div class="brand">Merrisol</div>

    <section class="back-content">
      <h1 class="title">Amber Hush<br>Mousse</h1>
      <h2 class="variant">Violet Base</h2>
      <p class="tan">Deep Mediterranean<br>Inspired Tan</p>
      <ul class="claims">
        <li><svg viewBox="0 0 22 22"><circle cx="10" cy="12" r="8" fill="none" stroke="#c0157a" stroke-width="2"/><path d="M5.5 11.5l4 4L20 3" fill="none" stroke="#c0157a" stroke-width="2.4" stroke-linecap="round" stroke-linejoin="round"/></svg>Easy to Apply &amp; Streak Free</li>
        <li><svg viewBox="0 0 22 22"><circle cx="10" cy="12" r="8" fill="none" stroke="#c0157a" stroke-width="2"/><path d="M5.5 11.5l4 4L20 3" fill="none" stroke="#c0157a" stroke-width="2.4" stroke-linecap="round" stroke-linejoin="round"/></svg><span>Vegan friendly &amp; 100% natural<br>DHA tan actives</span></li>
      </ul>
      <div class="info">
        <span class="pill">USING:</span>
        <p>Lorem ipsum dolor sit amet, consectetuer adipiscing elit. Maecenas porttitor congue massa. Fusce posuere, magna sed pulvinar ultricies, purus lectus malesuada libero, sit amet commodo magna eros quis urna.<br>Nunc viverra imperdiet enim. Fusce est. Vivamus a tellus.<br>Pellentesque habitant morbi tristique senectus et netus et malesuada fames ac turpi egestas. Proin pharetra nonummy pede. Mauris et orci.</p>
        <span class="pill">WARNING:</span>
        <p>This product does not contain a sunscreen and will not protect against sunburn. For external use only. If skin irritation occurs, discontinue use. Carry out a patch test 24 hours prior to full body use. Store below 25°C.</p>
        <span class="pill">INGREDIENTS:</span>
        <p>Water (Aqua), Propylene Glycol, Dihydroxyacetone, Peg-6 Caprylic/Capric Glycerides, Dihydroxypropyl Peg-5 Linoleammonium Chloride, Peg-7 Glyceryl Cocoate, Caramel, Phenoxyethanol, Caprylyl Glycol, Potassium Sorbate, Hexylene Glycol, Glycerin, Helianthus Annuus (Sunflower) Seed Oil, Beta Vulgaris (Beet) Root Extract, Panthenol, Solanum Lycopersicum (Tomato) Fruit Extract, Vaccinium Macrocarpon (Cranberry) Fruit Extract, L-ascorbic Acid (Vitamin C), Tocopheryl Acetate (Vitamin E), Theobroma Cacao (Cocoa) Seed Butter, Rosa Canina (Rose Hip) Fruit Oil, Glycine Soja (Soybean) Oil, Cucumis Sativus (Cucumber) Fruit Extract, Blue 1 (CI 42090), Red 40 (CI 16035), Yellow 6 (CI 15985), Green 5 (CI 61570), Yellow 5 (CI 19140), Red 33 (CI 17200).</p>
      </div>
    </section>

    <section class="front-content">
      <h1 class="title">Amber Hush</h1>
      <h2 class="variant">Violet Base</h2>
      <div class="tags">
        <div class="tag tag--time">1 Hour Sunless Mousse</div>
        <div class="tag tag--promise">The No Orange Guarantee!</div>
        <div class="tag tag--vegan">Vegan Formula</div>
      </div>
      <p class="size">200ml 6.7 Fl Oz</p>
    </section>
  </div>

  <svg class="dieline" viewBox="0 0 1128 955" aria-hidden="true">
    <g fill="none" stroke="var(--cut)" stroke-width="1.6" stroke-dasharray="8 6">
      <rect x="73" y="72" width="982" height="811"/>
      <line x1="92" y1="72" x2="92" y2="883"/>
      <line x1="451" y1="72" x2="451" y2="883"/>
      <line x1="595" y1="72" x2="595" y2="883"/>
      <line x1="953" y1="72" x2="953" y2="883"/>
    </g>
    <g stroke="var(--cut)" stroke-width="3">
      <line x1="0" y1="60" x2="1128" y2="60"/>
      <line x1="0" y1="895" x2="1128" y2="895"/>
      <line x1="62" y1="0" x2="62" y2="955"/>
      <line x1="1067" y1="0" x2="1067" y2="955"/>
    </g>
  </svg>
</div>
</body>
</html>
```